A new presentation to our clients

we are a Real Estate agency, our website is www.lumibrasa.com and it’s time to have a new, fashion and remarcable Business Card. we want to differentiate ourselves from other companies so we want a business card that differentiates us. we want the business card to impact our customers. in the competitive market that we have today, we have to be different and it is this difference that we seek

Target Market(s)

Real Estate Clients

Contact Information for Business Card

We search a totaly diferent card from the usual

Font styles to use
Sans Serif

Colors
e34197

Requirements
Must have
• Logo, adress, phone contact, e-mail, photo, and our website
Nice to have
• We would like to see a modern business card
Should not have
• Houses or building draws

```html
<!DOCTYPE html>
<html lang="en">
<head>
<meta charset="utf-8">
<title>Lumi Brasa – Business Card</title>
<link rel="stylesheet" href="https://fonts.googleapis.com/css2?family=Cabin:wght@400;600&display=swap">
<style>
  :root {
    --brand-pink: #e8226e;
    --card-white: #ffffff;
    --text-grey: #4a4a4a;
    --backdrop: #e4e4e4;
  }
  html, body {
    margin: 0;
    padding: 0;
    width: 1200px;
    height: 791px;
    overflow: hidden;
    background: var(--backdrop);
    font-family: "Cabin", sans-serif;
  }
  .card {
    position: absolute;
    left: 158px;
    top: 143px;
    width: 884px;
    height: 504px;
    background: var(--card-white);
    border-radius: 30px;
    overflow: hidden;
  }
  .card__bands {
    position: absolute;
    inset: 0;
  }
  .card__bands path { fill: var(--brand-pink); }
  .holder {
    position: absolute;
    left: 61px;
    top: 28px;
    color: var(--card-white);
  }
  .holder__name {
    margin: 0;
    font-size: 34px;
    font-weight: 400;
    letter-spacing: 0.5px;
    line-height: 1.1;
  }
  .holder__role {
    margin: 2px 0 0 4px;
    font-size: 20px;
    font-weight: 600;
  }
  .address {
    position: absolute;
    left: 54px;
    top: 217px;
    margin: 0;
    font-style: normal;
    font-size: 19.5px;
    line-height: 26px;
    color: var(--text-grey);
  }
  .contacts {
    position: absolute;
    left: 60px;
    top: 281px;
    margin: 0;
    padding: 0;
    list-style: none;
    font-size: 19.5px;
    line-height: 25.5px;
    color: var(--text-grey);
  }
  .contacts__label { color: var(--brand-pink); }
  .brand-name {
    position: absolute;
    left: 412px;
    top: 238px;
    margin: 0;
    font-size: 70px;
    font-weight: 600;
    color: var(--brand-pink);
    letter-spacing: 1px;
  }
  .website {
    position: absolute;
    left: 538px;
    top: 446px;
    font-size: 21px;
    letter-spacing: 2.5px;
    color: var(--card-white);
  }
</style>
</head>
<body>
  <main class="card">
    <svg class="card__bands" width="884" height="504" viewBox="0 0 884 504" aria-hidden="true">
      <path d="M0 0 H405 C405 90 372 140 305 140 H0 Z"/>
      <path d="M452 504 C472 450 512 424 566 424 H884 V504 Z"/>
    </svg>

    <header class="holder">
      <h1 class="holder__name">MARTA REIS</h1>
      <p class="holder__role">CEO/FOUNDER</p>
    </header>

    <address class="address">
      Rua das Flores Altas, 118<br>
      4150-262, Porto Alto
    </address>

    <ul class="contacts">
      <li><span class="contacts__label">Phone :</span> (+351) 221 480 356</li>
      <li><span class="contacts__label">Fax :</span> (+351) 221 480 357</li>
      <li><span class="contacts__label">Emai :</span> geral@lumibrasa.com</li>
    </ul>

    <p class="brand-name">Lumi Brasa</p>

    <div class="website">www.lumibrasa.com</div>
  </main>
</body>
</html>
```